Sunscreen Package Design Modern SPF 50

Update current package design to a more modern design target women 16-40 Do not make it playful. SOLANA VISTAS is home to movie stars and high income business people PalmSprings is one of the most desired vacation areas in the world. The sun shines 350 days a year. World class Tennis and Golf tournaments are held every year with the worlds top players attending these tournaments

Target Market(s)

Women

Industry/Entity Type

Skin Protection

Font styles to use
Sans Serif

Requirements
Must have
• The words SOLANA VISTAS and KORIVELL

```html
<!DOCTYPE html>
<html lang="en">
<head>
<meta charset="utf-8">
<title>Solana Vistas KORIVELL SPF 50</title>
<link rel="stylesheet" href="https://fonts.googleapis.com/css2?family=Gilda+Display&family=Montserrat:wght@400;500&display=swap">
<style>
  :root {
    --backdrop: #e6e6e6;
    --label: #e6ddd1;
    --ink: #3a302c;
    --terracotta: #c0582f;
    --cap: #bd552f;
  }
  * { margin: 0; padding: 0; box-sizing: border-box; }
  html, body { width: 1200px; height: 912px; overflow: hidden; }
  body { background: var(--backdrop); position: relative; font-family: "Montserrat", sans-serif; color: var(--ink); }
  .tube-label {
    position: absolute; left: 453px; top: 93px; width: 300px; height: 623px;
    background: var(--label); border-radius: 3px 3px 10px 10px;
  }
  .tube-cap {
    position: absolute; left: 516px; top: 716px; width: 174px; height: 109px;
    background: var(--cap); border-radius: 0 0 6px 6px;
  }
  .label-item { position: absolute; left: 0; width: 100%; text-align: center; line-height: 1; white-space: nowrap; }
  .brand-line { font-family: "Montserrat", sans-serif; font-weight: 500; color: var(--ink); }
  .brand-line.first { top: 146px; font-size: 36px; letter-spacing: 1px; }
  .brand-line.second { top: 190px; font-size: 36px; letter-spacing: 1px; }
  .brand-line.third { top: 239px; font-size: 16px; letter-spacing: 4.5px; padding-left: 4px; }
  .divider { position: absolute; left: 149.5px; top: 274px; width: 1px; height: 90px; background: var(--ink); }
  .category { top: 385px; font-size: 11px; font-weight: 500; letter-spacing: 2px; }
  .spf-label { top: 424px; font-size: 15px; font-weight: 500; color: var(--terracotta); }
  .spf-value { top: 440px; font-family: "Gilda Display", serif; font-size: 46px; color: var(--terracotta); }
  .claim { font-size: 9.5px; font-weight: 500; }
  .claim.uv { top: 500px; }
  .claim.spectrum { top: 517px; letter-spacing: 1px; }
  .claim.water { top: 536px; }
  .volume { top: 592px; font-size: 10px; font-weight: 500; }
</style>
</head>
<body>
  <div class="tube-label">
    <div class="label-item brand-line first">SOLANA</div>
    <div class="label-item brand-line second">VISTAS</div>
    <div class="label-item brand-line third">KORIVELL</div>
    <div class="divider"></div>
    <div class="label-item category">LUXURY SUNCARE</div>
    <div class="label-item spf-label">SPF</div>
    <div class="label-item spf-value">50</div>
    <div class="label-item claim uv">UVA + UVB PROTECTION</div>
    <div class="label-item claim spectrum">BROAD SPECTRUM</div>
    <div class="label-item claim water">WATER RESISTANT (80 MINUTES)</div>
    <div class="label-item volume">3 FL OZ / 88 mL</div>
  </div>
  <div class="tube-cap"></div>
</body>
</html>
```